Business card for Eyelash extension salon in CRESTMOOR HILLS,California USA

We need new business card for our salon in CRESTMOOR HILLS. The salon name is 'Lashvera' . We would like to have...Business name: Lashvera Name of person: will provide later Address 4720 N.Alder Crest Ave CRESTMOOR HILLS , CA 90210 Phone: will provide later (Text only) Web: www.lashverastudio.example Snapgrid icon, Circlebook icon follow us for seasonal campaign and news @lashverastudiolounge Design should look elegant, high-end, clean, simple, cohesive with my brand. Please refer my brand board. Business name color will be metallic bronzy color. Im thinking grey background or white background. Thanks

Target Market(s)

25-35. Gender neutral. People who are in Entertainment business industry.
This is High-end Eyelash extension salon in CRESTMOOR HILLS

Industry/Entity Type

Beauty Salon

Contact Information for Business Card

Business name: Lashvera
Name of person: will provide later
Address 4720 N.Alder Crest Ave CRESTMOOR HILLS , CA 90210
Phone: will provide later (Text only)
Web: www.lashverastudio.example
Snapgrid icon, Circlebook icon
follow us for seasonal campaign and news @lashverastudiolounge

Requirements
Must have
• Beautiful, elegant, clean and simple look but very attractive and modern
Should not have
• We don't like too clutter, too busy designs.

```html
<!DOCTYPE html>
<html lang="en">
<head>
<meta charset="utf-8">
<title>Lashvera Business Card</title>
<link rel="stylesheet" href="https://fonts.googleapis.com/css2?family=Merriweather:wght@300;400;700&display=swap">
<style>
  :root {
    --page: #e3e3e3;
    --card-white: #ffffff;
    --bronze: #86644a;
    --grey-text: #a9a9a9;
    --ink: #4a4a4a;
    --divider: #cfcfcf;
    --band-grey: #a8a8a8;
    --silver-light: #cfcfcf;
    --silver-dark: #a9a9a9;
    --gold: #e8c65a;
    --white: #ffffff;
  }
  * { margin: 0; padding: 0; box-sizing: border-box; }
  html, body { width: 1200px; height: 960px; overflow: hidden; }
  body {
    background: var(--page);
    font-family: "Merriweather", Georgia, serif;
    position: relative;
  }
  .card { position: absolute; width: 600px; height: 343px; overflow: hidden; }

  /* Front */
  .card-front { left: 302px; top: 122px; background: var(--card-white); }
  .brand-block {
    position: absolute; left: 40px; top: 118px; width: 250px; text-align: center;
  }
  .brand-name {
    font-weight: 400; font-size: 46px; color: var(--bronze); line-height: 1;
  }
  .brand-place {
    margin-top: 10px; font-weight: 300; font-size: 8px; letter-spacing: 2px; color: var(--bronze);
  }
  .divider {
    position: absolute; left: 299px; top: 91px; width: 1px; height: 162px; background: var(--divider);
  }
  .contact { position: absolute; left: 326px; top: 92px; color: var(--ink); }
  .person-name { font-weight: 700; font-size: 23px; color: var(--bronze); letter-spacing: 1px; line-height: 1.05; }
  .person-role { font-weight: 700; font-size: 14px; color: var(--grey-text); letter-spacing: 1px; line-height: 1.1; }
  .address, .reach { font-weight: 300; font-size: 13.5px; line-height: 19px; }
  .address { margin-top: 14px; }
  .reach { margin-top: 8px; }
  .band { position: absolute; left: 0; bottom: 0; width: 600px; height: 11px; }

  /* Back */
  .card-back {
    left: 299px; top: 495px;
    background: linear-gradient(160deg, var(--silver-light) 0%, #bdbdbd 55%, var(--silver-dark) 100%);
  }
  .back-brand { position: absolute; left: 0; top: 100px; width: 100%; text-align: center; }
  .back-name { font-weight: 400; font-size: 64px; color: var(--gold); line-height: 1; }
  .back-place { margin-top: 16px; font-weight: 300; font-size: 8px; letter-spacing: 2px; color: var(--gold); }
  .social {
    position: absolute; left: 0; top: 288px; width: 100%;
    display: flex; justify-content: center; gap: 14px;
    list-style: none; font-size: 10px; font-weight: 400; color: var(--white);
  }
</style>
</head>
<body>
  <section class="card card-front" aria-label="Card front">
    <div class="brand-block">
      <div class="brand-name">Lashvera</div>
      <div class="brand-place">CRESTMOOR HILLS</div>
    </div>
    <div class="divider"></div>
    <div class="contact">
      <div class="person-name">MIREI</div>
      <div class="person-role">OWNER</div>
      <div class="address">4720 N.Alder Crest Ave<br>Crestmoor Hills, CA 90512</div>
      <div class="reach">310.555.0142<br>hello@lashverastudio.example<br>www.lashverastudio.example</div>
    </div>
    <svg class="band" viewBox="0 0 600 11" preserveAspectRatio="none">
      <polygon points="0,0 393,0 389,11 0,11" fill="var(--bronze)"/>
      <polygon points="396,0 600,0 600,11 392,11" fill="var(--band-grey)"/>
    </svg>
  </section>

  <section class="card card-back" aria-label="Card back">
    <div class="back-brand">
      <div class="back-name">Lashvera</div>
      <div class="back-place">CRESTMOOR HILLS</div>
    </div>
    <ul class="social">
      <li>Circlebook</li>
      <li>Snapgrid</li>
      <li>Reviewly</li>
    </ul>
  </section>
</body>
</html>
```